Recto Verso Audiology Business Card

Business card with a beautiful design on the back. On the Recto you need the following data Lindqvist Oren Audiologist Hearing Solutions Hearing Protection Tinnitus Hyperacusis Tel: 0482/37 59 08 Email: On the back, you need something nice like the attached file. The logo "Corra Luna" can be in the center The colors of the Logo can not be changed If possible stay in the same colors as the logo Another solution is to put the logo on the front and have a nice back (A mosaic of small ears, hearing aids or other ..) Thank you _______________________________________________________________ Visit card On the Recto Lindqvist Oren Audiologist Hearing Solutions Hearing Protection Tinnitus Hyperacusis Tel: 0482/37 59 08 Email: You can put the logo " Corra Luna "on the Recto of the Verso The colors of the logo can not be changed. If you put the logo on the back, it must be well integrated. On the Verso I need something in the files. something stylish. It's a visit card for an audiologist. You can get ears of hearing aids if you need. Thanks

Target Market(s)

customers

Contact Information for Business Card

Carte de visite standard ou A6

Font styles to use
Serif
Sans Serif

Colors
33a6d7

Requirements
Must have
• the logo and a stylized background.
Nice to have
• It would be nice to have a back side related to audiology (ears, hearing aids etc.)

```html
<!DOCTYPE html>
<html lang="en">
<head>
<meta charset="utf-8">
<title>Corra Luna – Audiology Business Card</title>
<link rel="stylesheet" href="https://fonts.googleapis.com/css2?family=Roboto:wght@400;500&display=swap">
<style>
  :root {
    --stage: #e9e7e4;
    --card: #242424;
    --card-edge: #1b1b1b;
    --accent: #3fb8d4;
    --muted: #5d6a73;
    --text: #f1f1f1;
    --rule: #3a3a3a;
    --pattern-a: #1f2a2c;
    --pattern-b: #253a3f;
  }
  * { box-sizing: border-box; margin: 0; padding: 0; }
  html, body { width: 1200px; height: 419px; overflow: hidden; }
  body {
    background: var(--stage);
    font-family: "Roboto", Arial, sans-serif;
    position: relative;
  }
  .card {
    position: absolute;
    top: 47px;
    width: 500px;
    height: 324px;
    background: var(--card);
    border: 1px solid var(--card-edge);
    border-radius: 3px;
    overflow: hidden;
  }
  .card--verso { left: 70px; }
  .card--recto { left: 630px; }

  .ear-pattern {
    position: absolute;
    inset: 0;
    background: radial-gradient(circle at 50% 50%, var(--pattern-b), var(--pattern-a) 75%);
  }

  .brand {
    position: absolute;
    display: flex;
    align-items: center;
    gap: 12px;
    color: var(--accent);
    font-weight: 500;
    letter-spacing: 1px;
    text-transform: uppercase;
  }
  .brand__square {
    width: 14px;
    height: 14px;
    background: var(--accent);
  }
  .card--verso .brand {
    left: 50%;
    top: 50%;
    transform: translate(-50%, -50%);
    font-size: 30px;
    background: var(--card);
    padding: 22px 28px;
  }
  .card--recto .brand {
    left: 40px;
    top: 135px;
    font-size: 22px;
  }

  .divider {
    position: absolute;
    left: 230px;
    top: 88px;
    width: 1px;
    height: 140px;
    background: var(--rule);
  }

  .person {
    position: absolute;
    left: 250px;
    top: 104px;
  }
  .person__name {
    color: var(--accent);
    font-size: 21px;
    font-weight: 500;
    text-transform: uppercase;
    letter-spacing: 0.3px;
  }
  .person__title {
    color: var(--muted);
    font-size: 15px;
    margin-top: 2px;
  }

  .contact {
    position: absolute;
    left: 250px;
    top: 166px;
    list-style: none;
  }
  .contact__item {
    display: flex;
    align-items: center;
    gap: 9px;
    color: var(--text);
    font-size: 14px;
    height: 21px;
  }
  .contact__icon { width: 12px; height: 12px; fill: var(--accent); flex: none; }

  .services {
    position: absolute;
    left: 40px;
    bottom: 34px;
    color: var(--text);
    font-size: 14px;
    letter-spacing: 0.2px;
  }
</style>
</head>
<body>

  <section class="card card--verso" aria-label="Card back">
    <div class="ear-pattern" role="img" aria-label="Repeating pattern of small stylised ears with sound waves in teal line art"></div>
    <div class="brand"><span class="brand__square"></span>Corra Luna</div>
  </section>

  <section class="card card--recto" aria-label="Card front">
    <div class="brand"><span class="brand__square"></span>Corra Luna</div>
    <div class="divider"></div>

    <div class="person">
      <p class="person__name">Lindqvist Oren</p>
      <p class="person__title">Audiologist Hearing</p>
    </div>

    <ul class="contact">
      <li class="contact__item">
        <svg class="contact__icon" viewBox="0 0 24 24"><path d="M6.6 10.8a15.1 15.1 0 0 0 6.6 6.6l2.2-2.2a1 1 0 0 1 1-.25 11.4 11.4 0 0 0 3.6.57 1 1 0 0 1 1 1V20a1 1 0 0 1-1 1A17 17 0 0 1 3 4a1 1 0 0 1 1-1h3.5a1 1 0 0 1 1 1c0 1.25.2 2.45.57 3.6a1 1 0 0 1-.25 1z"/></svg>
        0482/37 59 08
      </li>
      <li class="contact__item">
        <svg class="contact__icon" viewBox="0 0 24 24"><path d="M2 5h20v14H2z M2 5l10 8 10-8" /><path d="M3 6.2l9 7.2 9-7.2V18H3z" fill="var(--card)"/><path d="M3 7.4l9 7 9-7V18H3z"/></svg>
        info@corraluna.be
      </li>
      <li class="contact__item">
        <svg class="contact__icon" viewBox="0 0 24 24"><circle cx="12" cy="12" r="10"/><path d="M2 12h20M12 2c3 3 3 17 0 20M12 2c-3 3-3 17 0 20" stroke="var(--card)" stroke-width="1.6" fill="none"/></svg>
        www.corraluna.be
      </li>
    </ul>

    <p class="services">Solutions Hearing | Protection | Tinnitus | Hyperacusis</p>
  </section>

</body>
</html>
```